Website Design for Agency

We require a website for our new agency. We have created a brief with our content, copywriting and most graphical assets. We just need some great with layout and to add some flair.

Number of Pages Required

1 page

Font styles to use
Sans Serif

```html
<!DOCTYPE html>
<html lang="en">
<head>
<meta charset="utf-8">
<title>Story Proof Partners</title>
<link href="https://fonts.googleapis.com/css2?family=Roboto:wght@400;500;700&display=swap" rel="stylesheet">
<style>
:root{
  --ink:#111111;
  --text:#6b6b6b;
  --muted:#555555;
  --band:#f3f3f3;
  --art:#ececec;
  --line:#cfcfcf;
  --white:#ffffff;
}
*{box-sizing:border-box;margin:0;padding:0}
html,body{width:1200px;height:4283px;overflow:hidden;background:var(--white)}
body{position:relative;font-family:'Roboto',Arial,sans-serif;color:var(--ink)}
.abs{position:absolute}
.brand{left:111px;top:22px;font-size:20px;font-weight:500;line-height:25px}
.nav{top:36px;font-size:14px;font-weight:500}
.nav.active{border-bottom:3px solid var(--ink);padding-bottom:5px}
.hero-title{left:111px;top:236px;font-size:35px;font-weight:500;line-height:43px}
.body-text{font-size:14px;line-height:26px;color:var(--text)}
.hero-text{left:111px;top:335px;width:410px;font-size:13px;line-height:26px;color:#333;z-index:2}
.btn{position:absolute;height:47px;border-radius:24px;font-size:13px;font-weight:700;display:flex;align-items:center;justify-content:center;letter-spacing:.2px}
.btn.outline{border:2.5px solid var(--ink);background:var(--white);color:var(--ink)}
.btn.solid{background:var(--ink);color:var(--white)}
.dot{position:absolute;top:547px;width:11px;height:11px;border-radius:50%;background:#d4d4d4}
.dot.on{background:var(--ink)}
.art{position:absolute;background:var(--art);border-radius:14px}
.trusted{left:0;width:1200px;top:670px;text-align:center;font-size:20px;font-weight:500}
.logo{position:absolute;top:748px;font-size:17px;font-weight:500;color:var(--muted);white-space:nowrap}
.timeline{left:599px;top:889px;height:2011px;border-left:2px dotted #9a9a9a}
.node{position:absolute;left:567px;width:66px;height:66px;border-radius:50%;border:2px solid var(--ink);background:var(--white);display:flex;align-items:center;justify-content:center}
.node i{display:block;width:22px;height:22px;border:2px solid var(--ink);border-radius:5px}
.sec-title{font-size:35px;font-weight:500;line-height:43px}
.right{text-align:right}
.justify{text-align:justify}
.band{left:0;top:3000px;width:1200px;height:623px;background:var(--band)}
.band-title{left:0;width:1200px;top:3098px;text-align:center;font-size:33px;font-weight:500;line-height:43px}
.col-title{font-size:26px;font-weight:500}
.checks{list-style:none}
.checks li{position:relative;padding-left:26px;font-size:14px;line-height:26px;color:var(--text)}
.checks svg{position:absolute;left:0;top:7px}
.cta{left:0;width:1200px;top:3716px;text-align:center;font-size:20px;font-weight:700;line-height:42px;color:var(--ink)}
.card{position:absolute;top:3931px;width:228px;height:241px;border:1px solid var(--line);background:var(--white)}
.card .icon{position:absolute;left:19px;top:20px;width:76px;height:76px;border-radius:50%;background:var(--ink)}
.card p{position:absolute;left:24px;top:116px;width:190px;font-size:14px;line-height:26px;color:#333}
.footer{left:0;top:4230px;width:1200px;height:53px;background:var(--ink);color:var(--white)}
.social{position:absolute;top:14px;width:26px;height:26px;border:1.5px solid var(--white);border-radius:50%}
.copy{position:absolute;right:110px;top:17px;font-size:14px}
.code{position:absolute;right:48px;top:17px;font-size:11px}
</style>
</head>
<body>

<header>
  <div class="abs brand">Story Proof<br>Partners</div>
  <nav>
    <span class="abs nav active" style="left:657px">Home</span>
    <span class="abs nav" style="left:725px">Services</span>
    <span class="abs nav" style="left:810px">How it Works</span>
    <span class="abs nav" style="left:926px">Examples</span>
    <span class="abs nav" style="left:1019px">Contact us</span>
  </nav>
</header>

<section class="hero">
  <div class="art" style="left:580px;top:91px;width:484px;height:482px" role="img" aria-label="Line illustration of a person riding a rising growth arrow chart above plants"></div>
  <svg class="abs" style="left:108px;top:178px" width="48" height="46" viewBox="0 0 48 46" fill="none" stroke="#111" stroke-width="3" stroke-linecap="round">
    <path d="M4 8 Q36 6 42 40"/><path d="M4 20 Q26 20 30 40"/><path d="M4 31 Q14 31 17 40"/><circle cx="7" cy="39" r="3" fill="#111"/>
  </svg>
  <h1 class="abs hero-title">Win More Hearts with<br>Powerful Case Studies</h1>
  <p class="abs hero-text">Testimonial Videos, written PDF's, slides, one-pagers and social media content. We create spellbinding case study stories and videos that will drive business for your revenue team .</p>
  <a class="btn outline" style="left:116px;top:429px;width:156px">LEARN MORE &#10132;</a>
  <a class="btn solid" style="left:288px;top:429px;width:156px">&#9654; WATCH VIDEO</a>
  <span class="dot on" style="left:111px"></span>
  <span class="dot" style="left:125px"></span>
  <span class="dot" style="left:139px"></span>
  <span class="dot" style="left:153px"></span>
</section>

<section class="clients">
  <h2 class="abs trusted">Trusted by Hundreds of Top Companies</h2>
  <span class="logo" style="left:120px">Northwave Radio</span>
  <span class="logo" style="left:292px">Helix</span>
  <span class="logo" style="left:390px">Veranta</span>
  <span class="logo" style="left:560px">CareBridge</span>
  <span class="logo" style="left:706px">Summit Funds</span>
  <span class="logo" style="left:845px">Stride Athletic</span>
  <span class="logo" style="left:985px">Petrova</span>
</section>

<section class="services">
  <div class="abs timeline"></div>

  <div class="node" style="top:883px"><i></i></div>
  <h2 class="abs sec-title" style="left:652px;top:874px">Capture results, built trust<br>and win new business</h2>
  <p class="abs body-text justify" style="left:652px;top:975px;width:398px">Combining real-world results with social proof, one well-produced customer story with multiple marketing assets will do a LOT of the heavy lifting for your business sales...because it comes directly from the mouth of a happy human who loves what you do.</p>
  <div class="art" style="left:216px;top:881px;width:316px;height:224px" role="img" aria-label="Line illustration of a person working at a desk with a laptop and floating media icons"></div>

  <div class="node" style="top:1199px"><i></i></div>
  <h2 class="abs sec-title right" style="left:141px;top:1192px;width:403px">It's More Than Marketing</h2>
  <p class="abs body-text right" style="left:141px;top:1253px;width:403px">No more awful sales sheets and dull corporate announcements that tell people to spend their money without reason. Our team of Award-winning journalists ensure your case studies are authentic. They're real. They're raw. They give people a reason to trust you, and, more importantly, a reason to give you their business.</p>
  <div class="art" style="left:765px;top:1180px;width:157px;height:224px" role="img" aria-label="Line illustration of a person arranging charts and puzzle pieces"></div>

  <div class="art" style="left:138px;top:1502px;width:409px;height:268px;border-radius:27px;background:#e6e6e6" role="img" aria-label="Video thumbnail: line illustration of a person planting a flag on a mountain top"></div>
  <svg class="abs" style="left:160px;top:1527px" width="30" height="30" viewBox="0 0 30 30"><circle cx="15" cy="15" r="15" fill="#111"/><path d="M11 8 L22 15 L11 22Z" fill="#fff"/></svg>
  <div class="node" style="top:1508px"><i></i></div>
  <h2 class="abs sec-title" style="left:652px;top:1499px">Get a testimonial video<br>anywhere nationwide</h2>
  <p class="abs body-text justify" style="left:652px;top:1599px;width:398px">You get our team of pros to handle the outreach, the interviews, the field production (or remote) and all the editing, graphics and storytelling for a lot less than you think. Powerful, proven content that moves the needle.</p>
  <a class="btn outline" style="left:650px;top:1722px;width:156px">LEARN MORE &#10132;</a>
  <a class="btn solid" style="left:821px;top:1722px;width:186px">PLANS AND PRICING</a>

  <div class="node" style="top:1883px"><i></i></div>
  <h2 class="abs sec-title right" style="left:101px;top:1876px;width:443px">Don't settle for just a single<br>case study. Get a lot more.</h2>
  <p class="abs body-text right" style="left:141px;top:1969px;width:403px">Narrative stories with your customer as the hero is key to readability and persuasion. Get professionally wordsmithed case studies to upload to your website, social channels, and more with pride.</p>
  <a class="btn outline" style="left:188px;top:2092px;width:156px">LEARN MORE &#10132;</a>
  <a class="btn solid" style="left:359px;top:2092px;width:188px">PLANS AND PRICING</a>
  <div class="art" style="left:690px;top:1870px;width:282px;height:291px" role="img" aria-label="Line illustration of two people on a video call in separate windows"></div>

  <div class="node" style="top:2259px"><i></i></div>
  <h2 class="abs sec-title" style="left:652px;top:2250px">Promo &amp; Sales Collateral</h2>
  <p class="abs body-text justify" style="left:652px;top:2306px;width:398px">From one-sheets, slides, long, short, and ultra-short articles for your website, blog, or sales team. You are in good hands knowing the content you get back is marketing gold. All without the headaches.</p>
  <a class="btn solid" style="left:650px;top:2432px;width:186px">PLANS AND PRICING</a>
  <div class="art" style="left:216px;top:2244px;width:308px;height:266px" role="img" aria-label="Line illustration of people on a ladder building a web page layout"></div>

  <div class="node" style="top:2586px"><i></i></div>
  <h2 class="abs sec-title right" style="left:121px;top:2574px;width:423px">Need help promoting<br>your customer story? We<br>got you.</h2>
  <p class="abs body-text right" style="left:141px;top:2722px;width:403px">You get campaign level help from our team. Landing pages, lead capture forms, press releases &amp; PR outreach to 400+ organizations and 100,000 journalists. All done by former our in-house former reporters who know how it's done.</p>
  <a class="btn outline" style="left:188px;top:2855px;width:156px">LEARN MORE &#10132;</a>
  <a class="btn solid" style="left:359px;top:2855px;width:188px">PLANS AND PRICING</a>
  <div class="art" style="left:648px;top:2601px;width:416px;height:299px" role="img" aria-label="Line illustration of a team meeting around a table with presentation boards"></div>
</section>

<section>
  <div class="abs band"></div>
  <h2 class="abs band-title">100% stress-free case study<br>project management</h2>
  <h3 class="abs col-title" style="left:111px;top:3214px">Get More for Less</h3>
  <p class="abs body-text" style="left:111px;top:3253px;width:330px">Whether you manage the marketing yourself or or have an in-house marketing manager, getting case studies done can be time consuming and costly if you don't do it right. We believe partnering with a case study expert can help your business prosper and establish itself as an industry leader.</p>
  <div class="abs" style="left:452px;top:3221px;width:266px;height:299px;background:var(--white)" role="img" aria-label="Line illustration of a person relaxing under a palm tree on a beach"></div>
  <h3 class="abs col-title" style="left:738px;top:3214px">Free up your schedule</h3>
  <p class="abs body-text" style="left:738px;top:3253px;width:350px">Our team of experienced video producers and content creators use proven persuasion strategies to create attention-grabbing case studies.</p>
  <ul class="abs checks" style="left:738px;top:3349px;width:352px">
    <li><svg width="14" height="14" viewBox="0 0 14 14"><circle cx="7" cy="7" r="7" fill="#111"/><path d="M4 7.2l2 2 4-4.2" stroke="#fff" stroke-width="1.8" fill="none"/></svg>We provide respectful and proactive client management throughout each case study project.</li>
    <li><svg width="14" height="14" viewBox="0 0 14 14"><circle cx="7" cy="7" r="7" fill="#111"/><path d="M4 7.2l2 2 4-4.2" stroke="#fff" stroke-width="1.8" fill="none"/></svg>We produce quality assets that your client will love and protect your brand's reputation</li>
    <li><svg width="14" height="14" viewBox="0 0 14 14"><circle cx="7" cy="7" r="7" fill="#111"/><path d="M4 7.2l2 2 4-4.2" stroke="#fff" stroke-width="1.8" fill="none"/></svg>We save you countless hours of time and effort.</li>
    <li><svg width="14" height="14" viewBox="0 0 14 14"><circle cx="7" cy="7" r="7" fill="#111"/><path d="M4 7.2l2 2 4-4.2" stroke="#fff" stroke-width="1.8" fill="none"/></svg>We ensure your satisfaction with every piece of case study material we deliver</li>
  </ul>
</section>

<section>
  <p class="abs cta">Everything you need is right here. Avoid the headaches over case study copywriting<br>and testimonial video production. Get in touch</p>
  <a class="btn solid" style="left:504px;top:3823px;width:186px">PLANS AND PRICING</a>
  <div class="card" style="left:111px"><span class="icon"></span><p>Lorem ipsum dolor sit am et, consectetur adipisc ing elit, sed do eiusmod tempo incididunt labore</p></div>
  <div class="card" style="left:361px"><span class="icon"></span><p>Lorem ipsum dolor sit am et, consectetur adipisc ing elit, sed do eiusmod tempo incididunt labore</p></div>
  <div class="card" style="left:611px"><span class="icon"></span><p>Lorem ipsum dolor sit am et, consectetur adipisc ing elit, sed do eiusmod tempo incididunt labore</p></div>
  <div class="card" style="left:861px"><span class="icon"></span><p>Lorem ipsum dolor sit am et, consectetur adipisc ing elit, sed do eiusmod tempo incididunt labore</p></div>
</section>

<footer class="abs footer">
  <span class="social" style="left:111px"></span>
  <span class="social" style="left:146px"></span>
  <span class="social" style="left:181px"></span>
  <span class="social" style="left:216px"></span>
  <span class="copy">&copy; Copyrights 2022 Company name | All Rights Reserved</span>
  <span class="code">C38</span>
</footer>

</body>
</html>
```